Workshop PPT Update for AI Transformation Sessions

Our strategic consulting firm runs strategy workshops using slides as workshop exercises. These slides are used to communicate to the participants in advance, run the workshops and produce the final deliverable.

It is time for a design "upgrade". We'd like them to be more engaging, hipper and more interesting. These slides are utilitarian, so clean and usable is good. I have attached the example of what we have today. I have also attached an example of another company's slides that I like.

We can't rip off their design nor can we go away 100% from what we have. But I think it is possible to "update" our look to something closer to their look. Grey colors are fine with some color pop.

Slide styles needed are - 1) Cover Page, 2) Instructions Page, 3) Bullet list 4) Worksheet (place for participants to add content 5) Table, 6) Two column.

```html
<!DOCTYPE html>
<html lang="en">
<head>
<meta charset="utf-8">
<title>Kickoff &amp; Discovery – Workshop Deck</title>
<link href="https://fonts.googleapis.com/css2?family=Roboto:wght@400;500;700&family=Roboto+Condensed:wght@400;500&display=swap" rel="stylesheet">
<style>
  :root{
    --ink:#3d4150;
    --ink-soft:#55596a;
    --red:#ad3b3d;
    --slate:#4b5166;
    --line:#6a6d78;
    --paper:#ffffff;
  }
  *{margin:0;padding:0;box-sizing:border-box}
  html,body{width:1200px;height:4068px;overflow:hidden;background:var(--paper)}
  body{font-family:"Roboto",Arial,sans-serif;color:var(--ink);position:relative}
  .slide{position:absolute;left:82px;width:1037px;height:583px;background:var(--paper);
    box-shadow:0 2px 8px rgba(0,0,0,.18);overflow:hidden}
  .abs{position:absolute}
  .photo{position:absolute;top:0;left:0;height:100%;
    background:linear-gradient(135deg,#5b6175 0%,#4a5065 55%,#3d4357 100%)}
  .footer-mark{position:absolute;right:18px;bottom:14px;font-size:20px;color:var(--ink)}
  .footer-mark .bar{color:#999;font-size:13px;margin:0 6px}
  .footer-mark .pg{font-size:12px;color:var(--ink-soft)}
  .slide-title{position:absolute;font-size:38px;font-weight:700;color:var(--ink);white-space:nowrap}
  .red{color:var(--red)}

  /* cover */
  .cover .photo{width:100%}
  .cover-brand{left:50px;top:50px;font-size:58px;color:#fff}
  .cover-title{left:46px;top:206px;font-size:82px;font-weight:700;color:#fff;letter-spacing:-.5px;white-space:nowrap}
  .cover-sub{left:50px;top:318px;font-size:30px;color:#fff}

  /* table */
  .plan-table{position:absolute;left:32px;top:134px;width:973px;border-collapse:collapse;
    font-family:"Roboto Condensed",Arial,sans-serif;font-size:20px;color:var(--ink);text-align:center}
  .plan-table th{background:var(--red);color:#fff;font-weight:500;height:54px;border:1px solid var(--red)}
  .plan-table td{border:1px solid var(--line);height:79px;vertical-align:middle}
  .plan-table td.lvl{color:var(--red);width:48px;font-size:18px}
  .plan-table td.elem{font-weight:500}
  .plan-table small{display:block;font-size:14px;font-weight:400}

  /* split layouts */
  .split .photo{width:352px}
  .stop{left:0;width:352px;top:266px;text-align:center;font-size:40px;font-weight:700;color:#fff}
  .big-q{left:420px;top:106px;font-size:40px;font-weight:700;line-height:54px;color:var(--ink);width:590px}
  .dot-list{position:absolute;list-style:none;font-size:23px;color:var(--ink);line-height:31px}
  .dot-list li{position:relative;padding-left:30px;margin-bottom:3px}
  .dot-list li::before{content:"";position:absolute;left:0;top:8px;width:17px;height:17px;border-radius:50%;background:var(--red)}

  .panel-title{font-size:40px;font-weight:700;line-height:54px;color:#fff}
  .ov-meta{left:72px;top:212px;font-size:22px;line-height:37px;color:#fff}
  .ov-prep{left:72px;top:303px;font-size:22px;font-weight:700;color:#fff}
  .small-list{position:absolute;list-style:none;font-size:12px}
  .small-list li{position:relative;padding-left:14px;height:32px}
  .small-list li::before{content:"";position:absolute;left:2px;top:5px;width:5px;height:5px;border-radius:50%;background:currentColor}

  .step{position:absolute;left:423px;width:560px}
  .step .n{display:inline-block;width:46px;font-size:22px;font-weight:700;color:var(--ink)}
  .step .t{font-size:22px;font-weight:700;color:var(--red);white-space:nowrap}
  .step p{margin-left:46px;font-size:14px;line-height:20px;color:var(--ink);margin-top:2px;max-width:520px}

  /* two column */
  .col-left{left:48px}
  .col-head{font-size:21px;font-weight:700;color:var(--red)}
  .col-sub{font-size:23px;font-weight:700;color:var(--ink)}
  .tiny{font-size:11px;color:var(--ink)}

  /* worksheet */
  .tl-line{position:absolute;left:446px;top:50px;width:4px;height:436px;background:var(--ink)}
  .tl-item{position:absolute;left:421px;width:600px}
  .tl-item svg{position:absolute;left:0;top:0}
  .tl-item h4{position:absolute;left:73px;top:-12px;font-size:22px;font-weight:700;color:var(--ink);white-space:nowrap}
  .tl-item p{position:absolute;left:73px;top:17px;font-size:14px;line-height:22px;color:var(--ink);width:510px}
</style>
</head>
<body>

<svg width="0" height="0" style="position:absolute">
  <defs>
    <symbol id="tick" viewBox="0 0 54 54">
      <circle cx="27" cy="27" r="27" fill="#ad3b3d"/>
      <circle cx="27" cy="27" r="21" fill="none" stroke="#fff" stroke-width="2"/>
      <path d="M17 27 l7 7 l13 -14" fill="none" stroke="#fff" stroke-width="4" stroke-linecap="round" stroke-linejoin="round"/>
    </symbol>
  </defs>
</svg>

<!-- Cover -->
<section class="slide cover" style="top:95px">
  <div class="photo" role="img" aria-label="Photo of colleagues collaborating at a laptop, under a slate overlay"></div>
  <div class="abs cover-brand">Keystrata</div>
  <h1 class="abs cover-title">Kickoff &amp; Discovery</h1>
  <div class="abs cover-sub">Sizing &amp; Scoping AI Transformation</div>
</section>

<!-- Table -->
<section class="slide table-slide" style="top:753px">
  <h2 class="slide-title" style="left:48px;top:40px">Plan Structure</h2>
  <table class="plan-table">
    <tr><th colspan="2" style="width:211px">Level</th><th style="width:265px">Planning Element &amp; Definition</th><th style="width:248px">Accountability/Owner</th><th>Frequency of Modification</th></tr>
    <tr><td class="lvl">1</td><td>What (overall)</td><td class="elem">Strategic Priorities</td><td>N/A</td><td>3+ years</td></tr>
    <tr><td class="lvl">1.1</td><td>What (this year)</td><td class="elem">Goals<small>Outcomes &amp; Strategies</small></td><td>Executive Leadership</td><td>1-3 years</td></tr>
    <tr><td class="lvl">1.1.1</td><td rowspan="2">How</td><td class="elem">Key Performance Indicators<br>and/or Initiatives</td><td></td><td>1 year (w/ qrtly targets)</td></tr>
    <tr><td class="lvl" style="font-size:16px">1.1.1.1</td><td class="elem">Action Items</td><td></td><td>Quarterly/Monthly</td></tr>
  </table>
  <div class="footer-mark">Keystrata<span class="bar">|</span><span class="pg">02</span></div>
</section>

<!-- Bullet list -->
<section class="slide split bullet-slide" style="top:1412px">
  <div class="photo" role="img" aria-label="Photo of two business people reviewing a document, under a slate overlay"></div>
  <div class="abs stop">STOP!!</div>
  <div class="abs big-q">All process need the following (regardless of doing which workshops being conducted):</div>
  <ul class="dot-list" style="left:420px;top:300px;width:570px">
    <li>Mission &amp; Vision</li>
    <li>Strategic Goals &amp; 2024 OKRs (or priorities)</li>
    <li>AI Vision: How will AI enable you to multiply your mission?</li>
    <li>AI Guiding Principles</li>
  </ul>
  <div class="footer-mark">Keystrata<span class="bar">|</span><span class="pg">03</span></div>
</section>

<!-- Instructions -->
<section class="slide split instructions-slide" style="top:2072px">
  <div class="photo" role="img" aria-label="Photo of hands working over charts on a desk, under a slate overlay"></div>
  <div class="abs panel-title" style="left:74px;top:88px">Workshop<br>Overview</div>
  <div class="abs ov-meta"><b>Participants:</b> Execs<br><b>Duration:</b> 2 hrs.</div>
  <div class="abs ov-prep">Prep Work:</div>
  <ul class="small-list" style="left:72px;top:346px;color:#fff">
    <li>Org Strategy</li><li>2023 Goal Performance</li><li>Existing policies</li><li>Pre-thinking questions</li>
  </ul>
  <h2 class="slide-title" style="left:398px;top:44px">Workshop Flow</h2>
  <div class="step" style="top:114px"><span class="n">01.</span><span class="t">Confirm Company Direction</span><p>Recap organizational purpose, values, vision &amp; winning strategy.</p></div>
  <div class="step" style="top:180px"><span class="n">02.</span><span class="t">Develop AI Vision</span></div>
  <div class="step" style="top:234px"><span class="n">03.</span><span class="t">Develop AI Guiding Principles</span><p style="max-width:500px">Developed AI Guiding Principles, supporting policies to include approved tools.</p></div>
  <div class="step" style="top:316px"><span class="n">04.</span><span class="t">Agree on a Governance Approach</span><p>Agreed upon governance approach, structure, &amp; executive champion.</p></div>
  <div class="step" style="top:378px"><span class="n">05.</span><span class="t">Agree on a Training &amp; Learning Approach</span><p>Set approach to training &amp; continuous learning.</p></div>
  <div class="step" style="top:436px"><span class="n">06.</span><span class="t">Determine Rollout &amp; Communication</span><p>Organizational rollout &amp; continuous communication.</p></div>
  <div class="abs" style="left:398px;top:506px;font-size:14px;line-height:21px">Deliverables<br><b class="red" style="font-weight:500">Your Company's AI Playbook</b></div>
  <div class="footer-mark">Keystrata<span class="bar">|</span><span class="pg">04</span></div>
</section>

<!-- Two column -->
<section class="slide two-column-slide" style="top:2730px">
  <h2 class="slide-title" style="left:48px;top:50px">Creating your AI Guiding Principles</h2>
  <div class="abs col-left" style="top:130px">
    <div class="col-head">Your Existing Material</div>
    <ul class="small-list" style="position:static;margin-top:8px;margin-left:14px;color:var(--ink)">
      <li>Company Values</li><li>Current Policies (GDPR,CCPA, etc.)</li><li>Legal Guidance</li><li>OTHER</li>
    </ul>
  </div>
  <div class="abs col-left" style="top:301px"><div class="col-sub">Examples for Inspiration</div><div class="tiny">See next slides</div></div>
  <div class="abs col-left" style="top:366px"><div class="col-sub">Chatbot Prompts</div><div class="tiny">HERE</div></div>

  <div class="abs" style="left:419px;top:126px;width:590px;display:flex;gap:12px;align-items:flex-start">
    <span style="font-size:26px;font-weight:700;color:var(--red);white-space:nowrap">Purpose:</span>
    <span style="font-size:14px;line-height:21px;padding-top:6px;max-width:440px">To create behavioral statements that everyone is expected to adhere to.</span>
  </div>
  <div class="abs" style="left:419px;top:185px;font-size:26px;font-weight:700">Instructions:</div>
  <div class="step" style="top:232px"><span class="n">01.</span><span class="t">Create the Outline.</span><p>Determine the topics that need a principle.</p></div>
  <div class="step" style="top:299px"><span class="n">02.</span><span class="t">Audit the Outline.</span><p>Look at the current policies to determine if all topics are covered.</p></div>
  <div class="step" style="top:364px"><span class="n">03.</span><span class="t">Draft the Guiding Principles.</span></div>
  <div class="step" style="top:409px"><span class="n">04.</span><span class="t">Determine which GPs need detailed policies.</span></div>
  <div class="step" style="top:453px"><span class="n">05.</span><span class="t">Determine which AI Tools support the GPs.</span></div>
  <div class="step" style="top:497px"><span class="n">06.</span><span class="t">Finalize via a legal and executive review.</span></div>
  <div class="footer-mark">Keystrata<span class="bar">|</span><span class="pg">05</span></div>
</section>

<!-- Worksheet -->
<section class="slide split worksheet-slide" style="top:3390px">
  <div class="photo" role="img" aria-label="Photo of a desk with a coffee cup and notebook, under a slate overlay"></div>
  <div class="abs panel-title" style="left:72px;top:204px">AI Guiding<br>Principles</div>
  <div class="abs" style="left:74px;top:322px;font-size:13px;line-height:19px;color:#fff">What guides our decision-making<br>and approach?</div>
  <div class="tl-line"></div>
  <div class="tl-item" style="top:20px">
    <svg width="54" height="54"><use href="#tick"/></svg>
    <h4>Principle #1</h4><p>Complete perspective from Executives, Directors, Managers &amp; Staff. Conduct competitive analysis and customer research (optional).</p>
  </div>
  <div class="tl-item" style="top:134px">
    <svg width="54" height="54"><use href="#tick"/></svg>
    <h4>Principle #2</h4><p>Complete perspective from Executives, Directors, Managers &amp; Staff. Conduct competitive analysis and customer research (optional)</p>
  </div>
  <div class="tl-item" style="top:245px">
    <svg width="54" height="54"><use href="#tick"/></svg>
    <h4>Principle #3</h4><p>Complete perspective from Executives, Directors, Managers &amp; Staff. Conduct competitive analysis and customer research (optional).</p>
  </div>
  <div class="tl-item" style="top:350px">
    <svg width="54" height="54"><use href="#tick"/></svg>
    <h4>Principle #4</h4><p>Complete perspective from Executives, Directors, Managers &amp; Staff. Conduct competitive analysis and customer research (optional).</p>
  </div>
  <div class="tl-item" style="top:458px">
    <svg width="54" height="54"><use href="#tick"/></svg>
    <h4>Principle #5</h4><p>Complete perspective from Executives, Directors, Managers &amp; Staff. Conduct competitive analysis and customer research (optional).</p>
  </div>
  <div class="footer-mark">Keystrata<span class="bar">|</span><span class="pg">06</span></div>
</section>

</body>
</html>
```